Harrowgate Supply and Trade, LLC

Would like an e-commerce website started

coldbrook bearings website is a business that is almost exactly like ours...I like how in the front of the website...their lines flash across the bottom...I have attached our line card to add some of ours

we are tolk certified...I would like that to show...... attached logo

also attached our logo

```html
<!DOCTYPE html>
<html lang="en">
<head>
<meta charset="utf-8">
<title>Harrowgate Supply and Trade, LLC</title>
<link href="https://fonts.googleapis.com/css2?family=Jost:wght@300;400;500;600;700&display=swap" rel="stylesheet">
<style>
:root{
  --green:#5a9a2e;
  --green-dark:#3f7a1f;
  --ink:#1d1d1d;
  --text:#555555;
  --line:#dcdcdc;
  --white:#ffffff;
  --footer:#1a1a1a;
}
*{margin:0;padding:0;box-sizing:border-box}
html,body{width:1200px;height:3568px;overflow:hidden}
body{position:relative;font-family:'Jost',sans-serif;color:var(--ink);background:var(--white)}
.abs{position:absolute}
.brand{display:flex;align-items:center;gap:10px;font-weight:600;font-size:24px;color:var(--ink)}
.brand .mark{width:22px;height:22px;background:var(--green)}
.header-contacts{display:flex;align-items:center;gap:26px;white-space:nowrap}
.contact-pill{display:flex;align-items:center;gap:12px;font-size:15px;font-weight:500;white-space:nowrap}
.contact-pill.phone{color:var(--green)}
.icon-circle{width:36px;height:36px;flex:0 0 36px;border-radius:50%;background:var(--ink);display:flex;align-items:center;justify-content:center}
.nav{display:flex;gap:28px;font-size:15px;color:#333;white-space:nowrap}
.nav .active{color:var(--green)}
.hero{left:0;top:118px;width:1200px;height:429px;background:linear-gradient(180deg,#6b5a45 0%,#8a7458 40%,#4c4035 100%);text-align:center;color:var(--white)}
.hero h1{font-weight:700;font-size:58px;line-height:66px;letter-spacing:1px;margin-top:115px}
.hero p{font-weight:300;font-size:50px;margin-top:12px;letter-spacing:.5px}
.section-title{font-weight:700;font-size:42px;letter-spacing:1px;display:flex;align-items:center;gap:10px;white-space:nowrap}
.divider{left:111px;width:978px;height:1px;background:var(--line)}
.photo{background:linear-gradient(160deg,#b8a78c,#5a4e42);}
.frame{border:1.5px solid var(--ink)}
.about-lead{font-size:23px;font-weight:500;line-height:35px}
.about-lead em{font-style:normal;color:var(--green)}
.about-body{font-size:15.5px;color:var(--text);line-height:30px}
.btn-green{background:var(--green);color:var(--white);font-size:15px;font-weight:500;display:flex;align-items:center;justify-content:center}
.card{top:1329px;width:297px;height:320px;border:2px solid #e3e3e3;text-align:center}
.card svg{margin-top:41px}
.card h3{font-size:18px;font-weight:500;line-height:27px;margin-top:26px;letter-spacing:.3px}
.card p{font-size:17px;color:var(--text);line-height:28px;margin-top:14px;padding:0 22px}
.product{top:1945px;width:216px;text-align:center}
.product .pic{height:280px}
.product .name{font-size:18px;margin-top:32px;color:#333}
.product .order{width:152px;height:39px;background:var(--ink);color:var(--white);margin:13px auto 0;font-size:16px;font-weight:500;display:flex;align-items:center;justify-content:center}
.catalog{left:111px;top:2419px;width:978px;height:320px;background:var(--green);color:var(--white)}
.store-line{display:flex;align-items:center;gap:12px;font-size:17px;line-height:24px;white-space:nowrap}
.footer{left:0;top:3310px;width:1200px;height:258px;background:var(--footer);color:var(--white);text-align:center}
.footer .brand{color:var(--white);justify-content:center}
.footer .nav{color:var(--white);justify-content:center;font-size:17px;gap:26px}
</style>
</head>
<body>

<svg width="0" height="0" style="position:absolute">
  <defs>
    <symbol id="gear" viewBox="0 0 40 34">
      <circle cx="14" cy="20" r="10" fill="#5a9a2e"/>
      <circle cx="14" cy="20" r="4" fill="#fff"/>
      <circle cx="30" cy="9" r="7" fill="#5a9a2e"/>
      <circle cx="30" cy="9" r="2.8" fill="#fff"/>
    </symbol>
    <symbol id="gear-light" viewBox="0 0 40 34">
      <circle cx="14" cy="20" r="10" fill="#fff"/>
      <circle cx="14" cy="20" r="4" fill="#5a9a2e"/>
      <circle cx="30" cy="9" r="7" fill="#fff"/>
      <circle cx="30" cy="9" r="2.8" fill="#5a9a2e"/>
    </symbol>
    <symbol id="mail" viewBox="0 0 20 20">
      <rect x="3" y="5" width="14" height="10" rx="1" fill="none" stroke="#fff" stroke-width="1.6"/>
      <path d="M3 6l7 5 7-5" fill="none" stroke="#fff" stroke-width="1.6"/>
    </symbol>
    <symbol id="phone" viewBox="0 0 20 20">
      <path d="M6 3l3 3-2 2c1 2 3 4 5 5l2-2 3 3-2 3C9 17 3 11 3 5z" fill="#fff"/>
    </symbol>
  </defs>
</svg>

<header>
  <div class="abs brand" style="left:111px;top:44px"><span class="mark"></span>Harrowgate</div>
  <div class="abs header-contacts" style="right:115px;top:21px">
    <div class="contact-pill">
      <span class="icon-circle"><svg width="20" height="20"><use href="#mail"/></svg></span>orders@hgsupply.com
    </div>
    <div class="contact-pill phone">
      <span class="icon-circle"><svg width="20" height="20"><use href="#phone"/></svg></span>555-014-2280
    </div>
  </div>
  <nav class="abs nav" style="right:112px;top:79px">
    <span class="active">Home</span><span>Products</span><span>Shop Catalog</span><span>Line Card</span><span>Promotions</span><span>Company Info</span>
  </nav>
</header>

<section class="abs hero" role="img" aria-label="Warehouse aisle with tall shelving and stacked boxes">
  <h1>HARROWGATE SUPPLY<br>AND TRADE LLC</h1>
  <p>WE KEEP PLANTS RUNNING</p>
</section>

<section>
  <h2 class="abs section-title" style="left:113px;top:632px">ABOUT US <svg width="40" height="34"><use href="#gear"/></svg></h2>
  <div class="abs frame" style="left:121px;top:729px;width:447px;height:317px"></div>
  <div class="abs photo" style="left:111px;top:721px;width:447px;height:316px" role="img" aria-label="Warehouse worker holding a parcel between tall shelves"></div>
  <p class="abs about-lead" style="left:654px;top:641px;width:440px">Perspiciatis unde omnis iste natus error luptatem <em>accsantium doloremqu</em> laudn tium, totam rapria.</p>
  <p class="abs about-body" style="left:654px;top:755px;width:440px">Lorem ipsum dolor sit amet, consecttur adipiscing elit, sed do eiusd tempor in cididunt ut labore dolore magna aliqua. Quis ipsum suse ultrces gravida. Risus commodo viverra maeci accumsan lacus vel facilisis.</p>
  <p class="abs about-body" style="left:654px;top:885px;width:440px">Sed ut perspiciatis unde omnis iste natus error luptatem accusantium doloremque laudantium, totam raperiam, eaque ipsa quae ab illo inventore.</p>
  <div class="abs btn-green" style="left:654px;top:1006px;width:130px;height:43px">Learn More</div>
</section>

<div class="abs divider" style="top:1148px"></div>

<section>
  <h2 class="abs section-title" style="left:0;width:1200px;justify-content:center;top:1225px">SERVICES WE PROVIDE <svg width="40" height="34"><use href="#gear"/></svg></h2>

  <div class="abs card" style="left:111px">
    <svg width="70" height="68" viewBox="0 0 70 68" fill="none" stroke="#333" stroke-width="2">
      <rect x="4" y="4" width="62" height="44" rx="2"/><path d="M4 14h62" stroke="#5a9a2e"/>
      <circle cx="22" cy="30" r="7" stroke="#5a9a2e"/><path d="M34 26h22M34 32h16"/>
      <path d="M35 48v10M20 62h30"/>
    </svg>
    <h3>COMPUTER-AIDED<br>DESIGN</h3>
    <p>Duist aute irure dolor induris rep rehen derit in voluptate at velit esse cillum dolore.</p>
  </div>

  <div class="abs card" style="left:452px">
    <svg width="70" height="68" viewBox="0 0 70 68" fill="none" stroke="#333" stroke-width="2">
      <path d="M10 6l8 8-4 4-8-8M18 14l40 40 6 8-8-6-40-40" stroke="#5a9a2e"/>
      <path d="M60 8a10 10 0 0 0-12 12L10 56l4 4 36-38a10 10 0 0 0 12-12l-6 6-6-2-2-6z"/>
    </svg>
    <h3>FABRICATION AND<br>INSTALLATION</h3>
    <p>Duist aute irure dolor induris rep rehen derit in voluptate at velit esse cillum dolore.</p>
  </div>

  <div class="abs card" style="left:791px">
    <svg width="70" height="68" viewBox="0 0 70 68" fill="none" stroke="#333" stroke-width="2">
      <rect x="8" y="2" width="54" height="64" rx="2"/><path d="M8 12h54" stroke="#5a9a2e"/>
      <path d="M16 24h22M16 34h22M16 44h22M16 54h22"/>
      <path d="M44 30l4 4 8-8M44 48l4 4 8-8" stroke="#5a9a2e"/>
    </svg>
    <h3>PLANT SURVEYS</h3>
    <p>Duist aute irure dolor induris rep rehen derit in voluptate at velit esse cillum dolore.</p>
  </div>
</section>

<div class="abs divider" style="top:1759px"></div>

<section>
  <h2 class="abs section-title" style="left:0;width:1200px;justify-content:center;top:1833px">FEATURED PRODUCTS <svg width="40" height="34"><use href="#gear"/></svg></h2>

  <svg class="abs" style="left:42px;top:2070px" width="28" height="20" viewBox="0 0 28 20" fill="none" stroke="#777" stroke-width="2"><path d="M26 10H3M11 2L3 10l8 8"/></svg>
  <svg class="abs" style="left:1131px;top:2070px" width="28" height="20" viewBox="0 0 28 20" fill="none" stroke="#1d1d1d" stroke-width="2"><path d="M2 10h23M17 2l8 8-8 8"/></svg>

  <div class="abs product" style="left:111px">
    <div class="pic" style="background:linear-gradient(150deg,#6d5a3a,#2b2522)" role="img" aria-label="Close view of a roller bearing"></div>
    <div class="name">Bearings</div><div class="order">ORDER NOW</div>
  </div>
  <div class="abs product" style="left:365px">
    <div class="pic" style="background:radial-gradient(circle at 55% 45%,#b5b5b5,#3a3a3a 60%,#0e0e0e)" role="img" aria-label="Brake disc with brake pads"></div>
    <div class="name">Brakes &amp; Clutches</div><div class="order">ORDER NOW</div>
  </div>
  <div class="abs product" style="left:619px">
    <div class="pic" style="background:linear-gradient(160deg,#4f6f9a,#a8373a 60%,#8c7a62)" role="img" aria-label="Red electric motor on a pallet"></div>
    <div class="name">Motors</div><div class="order">ORDER NOW</div>
  </div>
  <div class="abs product" style="left:873px">
    <div class="pic" style="background:linear-gradient(160deg,#9aa0a6,#d6d6d4 55%,#8e8a84)" role="img" aria-label="Braided metal hoses with flanged fittings"></div>
    <div class="name">Hose &amp; Fittings</div><div class="order">ORDER NOW</div>
  </div>
</section>

<section class="abs catalog">
  <h2 class="abs section-title" style="left:58px;top:56px;font-size:44px;color:var(--white);gap:4px">EQUIPMENT CATALOG <svg width="40" height="34"><use href="#gear-light"/></svg></h2>
  <p class="abs" style="left:58px;top:133px;font-size:16px;line-height:28px;width:600px">Don't miss out on this opportunity to take your business to the next level.<br>Browse our catalog today and start transforming your operations!</p>
  <div class="abs" style="left:58px;top:219px;width:130px;height:43px;border:2px solid var(--white);display:flex;align-items:center;justify-content:center;font-size:15px;font-weight:500">Shop Now</div>
  <div class="abs" style="left:693px;top:23px;width:197px;height:268px;background:linear-gradient(160deg,#2e3e52,#1f2b3a);box-shadow:6px 6px 10px rgba(0,0,0,.25)" role="img" aria-label="Printed catalog brochure cover"></div>
</section>

<div class="abs divider" style="top:2823px"></div>

<section>
  <h2 class="abs section-title" style="left:111px;top:2897px">OUR STORE <svg width="40" height="34" style="margin-left:8px"><use href="#gear"/></svg></h2>
  <div class="abs store-line" style="left:111px;top:2984px">
    <span class="icon-circle"><svg width="20" height="20"><use href="#mail"/></svg></span>
    <span>1187 Kestrel Lane<br>Alderton, VA 23990</span>
  </div>
  <div class="abs store-line" style="left:111px;top:3052px">
    <span class="icon-circle"><svg width="20" height="20"><use href="#mail"/></svg></span>orders@hgsupply.com
  </div>
  <div class="abs store-line" style="left:111px;top:3112px">
    <span class="icon-circle"><svg width="20" height="20"><use href="#phone"/></svg></span>555-014-2280
  </div>
  <div class="abs" style="left:111px;top:3183px;width:46px;height:46px;border:2px solid var(--green);border-radius:50%" aria-label="Social profile"></div>
  <div class="abs" style="left:172px;top:3183px;width:46px;height:46px;border:2px solid var(--green);border-radius:50%" aria-label="Social profile"></div>

  <div class="abs frame" style="left:643px;top:2912px;width:446px;height:317px"></div>
  <div class="abs photo" style="left:633px;top:2904px;width:447px;height:316px;background:linear-gradient(160deg,#8a98a6,#6a5a48 60%,#3e3833)" role="img" aria-label="Store staff member walking along a stocked warehouse aisle"></div>
  <div class="abs" style="left:481px;top:3113px;width:208px;height:82px;background:#ffffff;border:3px solid #4a2c7a" role="img" aria-label="Tolk certification badge"></div>
</section>

<footer class="abs footer">
  <div class="brand" style="margin-top:80px"><span class="mark"></span>Harrowgate</div>
  <nav class="nav" style="margin-top:40px">
    <span>Home</span><span>Products</span><span>Shop Catalog</span><span>Line Card</span><span>Promotions</span><span>Company Info</span>
  </nav>
  <p style="margin-top:18px;font-size:15px">2024 Harrowgate Supply and Trade LLC. All Rights Reserved.</p>
</footer>

</body>
</html>
```